Verodex business card

Business card for sustainable investment company called "Verodex". Verodex is an exchange platform selling carbon credits between buyers and sellers. Carbon Credits are an environmental commodity for reducing global carbon emissions.

the card should obviously have our logo and the theme should be sustainability/environment mixed with a trading platform.

Contact Information for Business Card

Logo, Name, Title, Phone, Email

Colors
0054AA
0677BA
7BADD7
CADEEF
E8F1F8
0094D4
00A9DD
6FCCEA
C7EBF8
E9F6FB
00AB8E
00BBA5
67D7C9
C6EFE9
E9F9F6
59FF00
82FF00
B8FF75
E3FFCB
F4FFEA

```html
<!DOCTYPE html>
<html lang="en">
<head>
<meta charset="utf-8">
<title>Verodex business card</title>
<link href="https://fonts.googleapis.com/css2?family=Montserrat:wght@400;500;600;700&display=swap" rel="stylesheet">
<style>
  :root {
    --backdrop: #d3d7d7;
    --kraft: #a17e5e;
    --kraft-edge: #8f6e50;
    --ink: #141d2b;
    --accent-blue: #2a5fc4;
    --mark-blue: #0094d4;
  }
  * { box-sizing: border-box; margin: 0; padding: 0; }
  html, body {
    width: 1200px;
    height: 1050px;
    overflow: hidden;
    background: var(--backdrop);
    font-family: "Montserrat", sans-serif;
  }
  .sheet {
    position: relative;
    width: 1200px;
    height: 1050px;
  }
  .card {
    position: absolute;
    left: 200px;
    width: 800px;
    height: 457px;
    background: var(--kraft);
    border: 1px solid var(--kraft-edge);
    color: var(--ink);
  }
  .card--front { top: 50px; }
  .card--back { top: 543px; }

  .brand {
    display: flex;
    align-items: center;
    justify-content: center;
  }
  .brand__square {
    background: var(--mark-blue);
  }
  .brand__name {
    font-weight: 600;
    letter-spacing: 0.04em;
    color: var(--ink);
  }

  .card--front .brand {
    height: 100%;
    gap: 30px;
  }
  .card--front .brand__square { width: 70px; height: 70px; }
  .card--front .brand__name { font-size: 74px; }

  .card--back {
    display: flex;
    flex-direction: column;
    align-items: center;
    padding-top: 62px;
    text-align: center;
  }
  .card--back .brand { gap: 16px; }
  .card--back .brand__square { width: 36px; height: 36px; }
  .card--back .brand__name { font-size: 40px; }

  .person__name {
    margin-top: 34px;
    font-size: 32px;
    font-weight: 700;
    letter-spacing: 0.08em;
    color: var(--accent-blue);
  }
  .person__title {
    margin-top: 4px;
    font-size: 19px;
    font-weight: 400;
    letter-spacing: 0.08em;
  }
  .contact {
    margin-top: 30px;
    font-size: 20px;
    line-height: 1.65;
  }
  .contact__row {
    display: flex;
    justify-content: center;
    gap: 28px;
  }
  .contact__item {
    display: inline-flex;
    align-items: center;
    gap: 9px;
  }
  .contact__icon {
    width: 16px;
    height: 16px;
    fill: var(--mark-blue);
  }
</style>
</head>
<body>
<main class="sheet">
  <section class="card card--front" aria-label="Card front">
    <div class="brand">
      <span class="brand__square"></span>
      <span class="brand__name">VERODEX</span>
    </div>
  </section>

  <section class="card card--back" aria-label="Card back">
    <div class="brand">
      <span class="brand__square"></span>
      <span class="brand__name">VERODEX</span>
    </div>
    <p class="person__name">DANIEL REYES</p>
    <p class="person__title">MANAGER</p>
    <div class="contact">
      <div class="contact__row">
        <span class="contact__item">
          <svg class="contact__icon" viewBox="0 0 16 16" aria-hidden="true"><path d="M3.2 1.2l2.4 2.6-1.3 1.9c.9 2 2.3 3.4 4.3 4.4l1.9-1.3 2.6 2.4-1.3 2.2C7.3 13.2 2.8 8.7 1 3.2z"/></svg>
          555-014-2290
        </span>
        <span class="contact__item">
          <svg class="contact__icon" viewBox="0 0 16 16" aria-hidden="true"><path d="M1 3h14v10H1z M1.8 3.6L8 8.6l6.2-5"/><path d="M1.8 3.6L8 8.6l6.2-5" stroke="#a17e5e" stroke-width="1.2" fill="none"/></svg>
          hello@verodexmail.com
        </span>
      </div>
      <div class="contact__row">
        <span class="contact__item">
          <svg class="contact__icon" viewBox="0 0 16 16" aria-hidden="true"><circle cx="8" cy="8" r="7"/><path d="M1 8h14M8 1c-3 3.5-3 10.5 0 14M8 1c3 3.5 3 10.5 0 14" stroke="#a17e5e" stroke-width="1" fill="none"/></svg>
          www.verodexhub.com
        </span>
      </div>
      <div class="contact__row">
        <span class="contact__item">27 Harbor Lane Westbrook Heights, OR 97012</span>
      </div>
    </div>
  </section>
</main>
</body>
</html>
```